Tollin Waste Website Design

Our new start-up needs a website design. We plan to help businesses find more sustainable ways to manage their waste. Our initial website aims to gather contact data from potential business customers and comprehensive information from waste facilities and waste transporters. We have a logo design (attached) which we would like included in the website design. I have also attached a number of pages that describe what information should appear on each page as well as a web design brief file that describes the look we are after.

```html
<!DOCTYPE html>
<html lang="en">
<head>
<meta charset="utf-8">
<title>Tollin Waste</title>
<link href="https://fonts.googleapis.com/css2?family=Montserrat:wght@400;500;700&family=Open+Sans:wght@400&display=swap" rel="stylesheet">
<style>
:root{
  --header-bg:#f4f4f4;
  --ink:#222;
  --brand-green:#5f9b28;
  --brand-green-dark:#4f8420;
  --nav-active:#5f9b28;
  --footer-bg:#1a1a1a;
  --footer-ink:#8a8a8a;
  --white:#fff;
  --scrim:rgba(0,0,0,.74);
}
*{box-sizing:border-box;margin:0;padding:0}
html,body{width:1200px;height:614px;overflow:hidden}
body{font-family:'Montserrat',sans-serif;background:#000;position:relative}

.site-header{position:absolute;left:0;top:0;width:1200px;height:92px;background:var(--header-bg)}
.brand{position:absolute;left:132px;top:24px;display:flex;align-items:center;gap:8px}
.brand-mark{width:38px;height:38px;border:3px solid var(--brand-green);border-radius:50%}
.brand-name{font-weight:700;font-size:22px;color:var(--ink);letter-spacing:.5px}
.main-nav{position:absolute;top:36px;left:655px;display:flex;gap:37px;font-size:15px;color:var(--ink)}
.main-nav a{color:inherit;text-decoration:none}
.main-nav a.active{color:var(--nav-active)}

.hero{position:absolute;left:0;top:92px;width:1200px;height:450px;
  background:linear-gradient(135deg,#6f7b76 0%,#a9aeb0 35%,#d8d6cf 55%,#8c8a7f 80%,#5c5a52 100%)}
.hero-title{position:absolute;top:280px;width:100%;text-align:center;font-weight:700;font-size:40px;color:var(--white);letter-spacing:.5px}
.hero-sub{position:absolute;top:336px;width:100%;text-align:center;font-weight:500;font-size:20px;color:var(--white)}
.audience{position:absolute;top:376px;left:132px;display:flex;gap:23px}
.audience a{width:297px;height:50px;border-radius:4px;background:var(--brand-green);color:var(--white);
  font-weight:700;font-size:19px;display:flex;align-items:center;justify-content:center;text-decoration:none}

.site-footer{position:absolute;left:0;top:542px;width:1200px;height:72px;background:var(--footer-bg);color:var(--footer-ink);font-size:11px}
.footer-links{position:absolute;left:133px;top:16px}
.footer-links span{margin:0 9px}
.copyright{position:absolute;left:133px;top:43px}
.social{position:absolute;right:132px;top:28px;display:flex;gap:16px}
.social span{width:18px;height:18px;border-radius:50%;background:var(--footer-ink)}

.scrim{position:absolute;inset:0;background:var(--scrim)}

.signup{position:absolute;left:0;top:0;width:1200px;height:614px;text-align:center;color:var(--white)}
.signup-brand{position:absolute;top:214px;left:0;width:100%;display:flex;justify-content:center;align-items:center;gap:8px}
.signup-brand .brand-mark{border-color:var(--white);width:44px;height:44px}
.signup-brand .brand-name{color:var(--white);font-size:25px}
.signup-text{position:absolute;top:284px;width:100%;font-weight:500;font-size:19px;line-height:29px}
.signup-form{position:absolute;top:354px;left:420px;display:flex;width:363px;height:48px}
.signup-form input{width:272px;height:48px;border:0;border-radius:5px 0 0 5px;padding:0 15px;
  font-family:'Open Sans',sans-serif;font-size:12px;color:#333;background:var(--white)}
.signup-form input::placeholder{color:#333}
.signup-form button{width:91px;height:48px;border:0;border-radius:0 5px 5px 0;background:var(--brand-green);
  color:var(--white);font-family:'Montserrat',sans-serif;font-size:17px;font-weight:500}
</style>
</head>
<body>
<header class="site-header">
  <div class="brand"><span class="brand-mark"></span><span class="brand-name">TOLLIN WASTE</span></div>
  <nav class="main-nav">
    <a class="active" href="#">About us</a><a href="#">What we do</a><a href="#">Resources</a><a href="#">Contact us</a>
  </nav>
</header>

<section class="hero" role="img" aria-label="Photograph of stacked waste drums and containers at a waste facility">
  <h1 class="hero-title">WELCOME TO TOLLIN WASTE</h1>
  <p class="hero-sub">Take control of your waste here:</p>
  <div class="audience">
    <a href="#">WASTE PRODUCERS</a><a href="#">WASTE FACILITIES</a><a href="#">WASTE TRANSPORTERS</a>
  </div>
</section>

<footer class="site-footer">
  <div class="footer-links">About us<span>|</span>What we do<span>|</span>Resources<span>|</span>Contact us</div>
  <div class="copyright">Copyright © 2018 Tollin Waste Management. All rights reserved.</div>
  <div class="social"><span></span><span></span></div>
</footer>

<div class="scrim"></div>

<section class="signup">
  <div class="signup-brand"><span class="brand-mark"></span><span class="brand-name">TOLLIN WASTE</span></div>
  <p class="signup-text">Welcome to Tollin Waste. We are just getting started.<br>Please register your email address to receive updates from us.</p>
  <form class="signup-form">
    <input type="email" placeholder="Email Address">
    <button type="button">SUBMIT</button>
  </form>
</section>
</body>
</html>
```